Velmora Freightway Solutions Business cards

Would like a very unique design catchy but professional for business cards. Please use log provided.Marlon WellsCeo and Founder TransCon Logistix Solutions1-888-913-3225mwells@tlsolutionsus.comwww.tlsolutionsus.com

```html
<!DOCTYPE html>
<html lang="en">
<head>
<meta charset="utf-8">
<title>Velmora Freightway Solutions – Business Cards</title>
<link rel="stylesheet" href="https://fonts.googleapis.com/css2?family=Open+Sans:wght@400;600;700&display=swap">
<style>
  :root {
    --brand-blue: #1273bd;
    --brand-red: #e8202a;
    --ink: #2b2b2b;
    --paper: #ffffff;
    --backdrop: #e8e5e1;
  }
  * { margin: 0; padding: 0; box-sizing: border-box; }
  html, body { width: 1200px; height: 960px; overflow: hidden; }
  body {
    position: relative;
    background: var(--backdrop);
    font-family: "Open Sans", Arial, sans-serif;
    color: var(--ink);
  }
  .card {
    position: absolute;
    background: var(--paper);
    border-radius: 36px;
    overflow: hidden;
    box-shadow: 0 2px 6px rgba(0,0,0,0.18);
  }
  .card-front { left: 237px; top: 47px; width: 720px; height: 406px; }
  .card-back { left: 247px; top: 502px; width: 705px; height: 406px; }

  /* Front */
  .front-name {
    position: absolute;
    left: 0; right: 0; top: 110px;
    text-align: center;
    font-weight: 700;
    font-size: 64px;
    line-height: 1.05;
    color: var(--brand-blue);
    letter-spacing: 1px;
  }
  .front-url {
    position: absolute;
    left: 115px; right: 115px; top: 357px;
    display: flex; align-items: center; gap: 12px;
    font-size: 17px; letter-spacing: 2.5px; color: #444;
  }
  .front-url .rule { flex: 1; height: 3px; background: var(--brand-blue); border-radius: 2px; }
  .front-url strong { color: var(--brand-blue); font-weight: 700; }

  /* Back */
  .brand-lockup {
    position: absolute; left: 60px; top: 38px;
    display: flex; align-items: center; gap: 14px;
  }
  .brand-square { width: 40px; height: 40px; background: var(--brand-red); }
  .brand-name {
    font-weight: 700; font-size: 27px; line-height: 1.15;
    color: var(--brand-blue); letter-spacing: 0.5px;
  }
  .contact-list {
    position: absolute; left: 58px; top: 218px;
    list-style: none; font-size: 16.5px; color: #222;
  }
  .contact-list li { display: flex; align-items: center; gap: 10px; height: 30px; }
  .contact-list svg { width: 14px; height: 14px; }
  .wave { position: absolute; left: 0; top: 0; }
  .holder {
    position: absolute; left: 440px; width: 230px; top: 320px;
    text-align: center; color: var(--paper);
  }
  .holder-name { font-weight: 600; font-size: 23px; letter-spacing: 0.3px; }
  .holder-title { font-size: 17px; margin-top: 8px; letter-spacing: 0.3px; }
</style>
</head>
<body>

<section class="card card-front">
  <div class="front-name">Velmora<br>Freightway Solutions</div>
  <div class="front-url">
    <span class="rule"></span>
    <span>www.<strong>vfwayroutes</strong>.com</span>
    <span class="rule"></span>
  </div>
</section>

<section class="card card-back">
  <svg class="wave" width="705" height="406" viewBox="0 0 705 406" aria-hidden="true">
    <path d="M0,252 C40,330 130,372 270,362 C430,350 560,262 705,272 V406 H0 Z" fill="var(--brand-blue)"/>
    <path d="M40,332 C170,392 390,360 540,300 C610,274 660,262 700,268" fill="none" stroke="var(--paper)" stroke-width="6"/>
  </svg>

  <div class="brand-lockup">
    <span class="brand-square"></span>
    <span class="brand-name">Velmora Freightway<br>Solutions</span>
  </div>

  <ul class="contact-list">
    <li>
      <svg viewBox="0 0 16 16"><path d="M4 1 L6.5 4.5 L5 6.5 C6 8.5 7.5 10 9.5 11 L11.5 9.5 L15 12 L13 15 C7 14 2 9 1 3 Z" fill="var(--brand-blue)"/></svg>
      1-888-470-6158
    </li>
    <li>
      <svg viewBox="0 0 16 16"><rect x="1" y="3" width="14" height="10" rx="1" fill="var(--brand-blue)"/><path d="M1.5 4 L8 9 L14.5 4" fill="none" stroke="#fff" stroke-width="1.3"/></svg>
      dpike@vfwayroutes.com
    </li>
    <li>
      <svg viewBox="0 0 16 16"><circle cx="8" cy="8" r="6.5" fill="none" stroke="var(--brand-blue)" stroke-width="1.3"/><ellipse cx="8" cy="8" rx="3" ry="6.5" fill="none" stroke="var(--brand-blue)" stroke-width="1.1"/><path d="M1.5 8 H14.5 M2.5 5 H13.5 M2.5 11 H13.5" stroke="var(--brand-blue)" stroke-width="1"/></svg>
      www.vfwayroutes.com
    </li>
  </ul>

  <div class="holder">
    <div class="holder-name">DORIAN PIKE</div>
    <div class="holder-title">CEO AND FOUNDER</div>
  </div>
</section>

</body>
</html>
```